Book Title: The Weaver's Lantern. Author Name: Maribel Trowcastle

We are needing a cover, spine and back cover design for a poetry book that we are publishing called The Weaver's Lantern. We are looking for an elegant, and simplistic design with a very natural, dynamic and powerful impact.

Design Idea #1 - Shiva Conch Shell with a pink or black background. See Paul Renwick Image attached for design inspiration. Simple and dynamic .
Title and Author name created in same style as the attached Paul Renwick's Harbors and Lanterns image.

Design Idea #2 - Image of cauldron on (see cauldrons attached for ideas) black background.
See Paul Renwick Image attached for design inspiration. Simple and dynamic Title and Author name created in same style as the attached Paul Renwick's Harbors and Lanterns image

Design Idea #3 - Image of Tree of Life (see attached images for idea of what we are looking for) Would like to see on plain white, green, black and green background.

Target Market(s)

Spiritual Women, healers, visionaries,Goddess'

Requirements
Must have
• Please see project descriptions for specific design concepts we are looking for. Please include the authors name: Maribel Trowcastle on front, spine and back cover of the book

```html
<!DOCTYPE html>
<html lang="en">
<head>
<meta charset="utf-8">
<title>The Weaver's Lantern — Cover Spread</title>
<link rel="stylesheet" href="https://fonts.googleapis.com/css2?family=Marcellus&family=EB+Garamond:wght@400&display=swap">
<style>
  :root {
    --page-bg: #ffffff;
    --cover-black: #000000;
    --spine-black: #050505;
    --spine-edge: #1a1a1a;
    --body-text: #f2f2f2;
    --silver-light: #f4f4f4;
    --silver-mid: #b9b9b9;
    --silver-dark: #7d7d7d;
    --art-gold: #a8a27a;
    --art-shadow: #1c1a10;
  }
  * { margin: 0; padding: 0; box-sizing: border-box; }
  html, body {
    width: 1200px; height: 1200px; overflow: hidden;
    background: var(--page-bg);
  }
  .spread {
    position: absolute;
    left: 40px; top: 214px;
    width: 1120px; height: 771px;
    display: flex;
    background: var(--cover-black);
  }
  .silver {
    background: linear-gradient(180deg, var(--silver-light) 0%, var(--silver-mid) 55%, var(--silver-dark) 100%);
    -webkit-background-clip: text;
    background-clip: text;
    color: transparent;
    font-family: "Marcellus", serif;
  }
  /* Back cover */
  .back-cover {
    width: 513px; height: 100%;
    position: relative;
  }
  .back-title {
    position: absolute; top: 70px; left: 0; right: 0;
    text-align: center;
    font-size: 27px; letter-spacing: 3px;
    font-weight: 400;
  }
  .back-title .small { font-size: 21px; }
  .blurb {
    position: absolute; top: 126px; left: 47px; width: 421px;
    font-family: "EB Garamond", serif;
    font-size: 15px; line-height: 21.4px;
    color: var(--body-text);
  }
  .blurb p {
    text-align: justify;
    text-align-last: center;
    margin-bottom: 21px;
  }
  .back-author {
    position: absolute; top: 690px; left: 0; right: 0;
    text-align: center;
    font-size: 24px; letter-spacing: 3px;
  }
  /* Spine */
  .spine {
    width: 94px; height: 100%;
    background: var(--spine-black);
    border-left: 1px solid var(--spine-edge);
    border-right: 1px solid var(--spine-edge);
    display: flex; justify-content: center;
    padding-top: 74px;
  }
  .spine-text {
    writing-mode: vertical-rl;
    white-space: nowrap;
    display: flex; align-items: center; gap: 40px;
  }
  .spine-title { font-size: 26px; letter-spacing: 2px; }
  .spine-title .small { font-size: 21px; }
  .spine-author {
    font-size: 20px; letter-spacing: 2.5px;
  }
  /* Front cover */
  .front-cover {
    width: 513px; height: 100%;
    position: relative;
    text-align: center;
  }
  .front-title {
    position: absolute; top: 66px; left: 0; right: 0;
    line-height: 1.12;
    letter-spacing: 6px;
    font-weight: 400;
  }
  .front-title .line-small { display: block; font-size: 38px; }
  .front-title .line-large { display: block; font-size: 49px; }
  .tree-art {
    position: absolute;
    left: 103px; top: 309px;
    width: 306px; height: 306px;
  }
  .front-author {
    position: absolute; top: 667px; left: 0; right: 0;
    font-size: 34px; letter-spacing: 4px;
  }
</style>
</head>
<body>
  <main class="spread">
    <section class="back-cover">
      <h2 class="back-title silver"><span class="small">THE</span> WEAVER'S LANTERN</h2>
      <div class="blurb">
        <p>Lorem ipsum dolor sit amet, consectetur adipiscing elit, sed do eiusmod tempor incididunt ut labore et dolore magna aliqua. Quis ipsum suspendisse ultrices gravida. Risus commodo viverra maecenas accumsan lacus vel facilisis. Lorem ipsum dolor sit amet, consectetur adipiscing elit, sed do eiusmod tempor incididunt ut labore et dolore magna aliqua. Quis ipsum suspendisse ultrices gravida. Risus commodo viverra maecenas accumsan lacus vel facilisis.</p>
        <p>Lorem ipsum dolor sit amet, consectetur adipiscing elit, sed do eiusmod tempor incididunt ut labore et dolore magna aliqua. Quis ipsum suspendisse ultrices gravida. Risus commodo viverra maecenas accumsan lacus vel facilisis. Lorem ipsum dolor sit amet, consectetur adipiscing elit, sed do eiusmod tempor incididunt ut labore et dolore magna aliqua. Quis ipsum suspendisse ultrices gravida. Risus commodo viverra maecenas accumsan lacus vel facilisis. Lorem ipsum dolor sit amet, consectetur adipiscing elit, sed do eiusmod tempor incididunt ut labore et dolore magna aliqua. Quis ipsum suspendisse ultrices gravida. Risus commodo viverra maecenas accumsan lacus vel facilisis.</p>
        <p>Lorem ipsum dolor sit amet, consectetur adipiscing elit, sed do eiusmod tempor incididunt ut labore et dolore magna aliqua. Quis ipsum suspendisse ultrices gravida. Risus commodo viverra maecenas accumsan lacus vel facilisis.</p>
      </div>
      <p class="back-author silver">Maribel Trowcastle</p>
    </section>

    <section class="spine">
      <div class="spine-text">
        <span class="spine-title silver"><span class="small">THE</span> WEAVER'S LANTERN</span>
        <span class="spine-author silver">Maribel Trowcastle</span>
      </div>
    </section>

    <section class="front-cover">
      <h1 class="front-title silver">
        <span class="line-small">THE</span>
        <span class="line-large">WEAVER'S</span>
        <span class="line-large">LANTERN</span>
      </h1>
      <svg class="tree-art" viewBox="0 0 306 306" role="img" aria-label="Carved stone medallion of a Tree of Life with leafy branches, lit in pale gold">
        <defs>
          <radialGradient id="medallion-tone" cx="50%" cy="45%" r="55%">
            <stop offset="0%" stop-color="#a8a27a"/>
            <stop offset="70%" stop-color="#6f6a4c"/>
            <stop offset="100%" stop-color="#1c1a10"/>
          </radialGradient>
        </defs>
        <circle cx="153" cy="153" r="150" fill="url(#medallion-tone)"/>
      </svg>
      <p class="front-author silver">Maribel Trowcastle</p>
    </section>
  </main>
</body>
</html>
```